Business Card Design

Business Card for professional consulting firm working with large financial institutions.

Target Market(s)

Executive buyers

Industry/Entity Type

Banking

Contact Information for Business Card

Mild creativity wanted. Not boring, but do elaborate artwork.

Font styles to use
Serif
Sans Serif

Colors

Designer to choose colors to be used in the design.

Requirements
Must have
• Standard business card features - company name, individual name, telephone, website, email, locations.
Nice to have
• Two colors
Should not have
• too many colors, fancy printing, cartoons.

```html
<!DOCTYPE html>
<html lang="en">
<head>
<meta charset="utf-8">
<title>k7advisory business card</title>
<link rel="stylesheet" href="https://fonts.googleapis.com/css2?family=Roboto:wght@400;500&family=Roboto+Condensed:wght@700&display=swap">
<style>
  :root {
    --backdrop: #2b2b2b;
    --card: #f1f1f1;
    --ink: #111111;
    --text: #3d3d3d;
    --muted: #9a9a9a;
    --rule: #7a7a7a;
    --band: #0a0a0a;
    --band-text: #ffffff;
  }
  html, body {
    margin: 0;
    padding: 0;
    width: 1200px;
    height: 960px;
    overflow: hidden;
    background: var(--backdrop);
    font-family: "Roboto", Arial, sans-serif;
  }
  .stage { position: relative; width: 1200px; height: 960px; }
  .card {
    position: absolute;
    width: 600px;
    height: 343px;
    background: var(--card);
    overflow: hidden;
  }
  .card--front { left: 314px; top: 113px; }
  .card--back  { left: 311px; top: 472px; }

  .brand-name {
    position: absolute;
    font-family: "Roboto", Arial, sans-serif;
    font-weight: 400;
    color: var(--ink);
    white-space: nowrap;
  }
  .card--front .brand-name { left: 78px; top: 56px; font-size: 30px; }
  .card--back .brand-name {
    left: 0; right: 0; top: 142px;
    text-align: center; font-size: 38px;
  }

  .person {
    position: absolute;
    right: 32px;
    top: 192px;
    text-align: right;
  }
  .person__name {
    font-family: "Roboto Condensed", "Arial Narrow", sans-serif;
    font-weight: 700;
    font-size: 24px;
    color: var(--ink);
    line-height: 1;
  }
  .person__title {
    font-family: "Roboto", Arial, sans-serif;
    font-weight: 500;
    font-size: 15px;
    color: var(--muted);
    margin-top: 4px;
    line-height: 1;
  }
  .divider {
    position: absolute;
    left: 36px;
    top: 228px;
    width: 411px;
    height: 1px;
    background: var(--rule);
  }

  .contacts {
    position: absolute;
    left: 32px;
    top: 259px;
    margin: 0; padding: 0;
    list-style: none;
    font-size: 14.5px;
    color: var(--text);
  }
  .contacts li {
    display: flex;
    align-items: center;
    height: 19px;
  }
  .contacts svg { width: 13px; height: 13px; margin-right: 8px; fill: var(--ink); }

  .address {
    position: absolute;
    right: 32px;
    top: 260px;
    text-align: right;
    font-size: 14.5px;
    line-height: 18px;
    color: var(--text);
    font-style: normal;
  }

  .web-band {
    position: absolute;
    left: 0; top: 276px;
    width: 600px; height: 30px;
    background: var(--band);
    color: var(--band-text);
    font-size: 15px;
    letter-spacing: 6.4px;
    text-align: center;
    line-height: 30px;
  }
</style>
</head>
<body>
<main class="stage">
  <section class="card card--front" aria-label="Card front">
    <div class="brand-name">k7advisory</div>

    <div class="person">
      <div class="person__name">DANIEL REYES</div>
      <div class="person__title">CEO/FOUNDER</div>
    </div>
    <div class="divider"></div>

    <ul class="contacts">
      <li>
        <svg viewBox="0 0 24 24" aria-hidden="true"><path d="M6.6 10.8a15.1 15.1 0 0 0 6.6 6.6l2.2-2.2c.3-.3.7-.4 1-.2 1.1.4 2.3.6 3.6.6.6 0 1 .4 1 1V20c0 .6-.4 1-1 1C10.6 21 3 13.4 3 4c0-.6.4-1 1-1h3.5c.6 0 1 .4 1 1 0 1.3.2 2.5.6 3.6.1.3 0 .7-.2 1z"/></svg>
        555 210 4830
      </li>
      <li>
        <svg viewBox="0 0 24 24" aria-hidden="true"><path d="M2 5h20v14H2z M3.5 6.5 12 13l8.5-6.5" fill="none" stroke="#111" stroke-width="0"/><path d="M2 5h20v2l-10 6L2 7z"/><path d="M2 9l10 6 10-6v10H2z"/></svg>
        info@k7advisory.com
      </li>
      <li>
        <svg viewBox="0 0 24 24" aria-hidden="true"><circle cx="12" cy="12" r="10"/><path d="M7 6c2 1 3 3 2 5s-3 2-3 4M15 4c-1 2 0 3 2 4s3 3 2 6M12 14c2 0 3 2 2 5" fill="none" stroke="#f1f1f1" stroke-width="1.6"/></svg>
        www.k7advisory.com
      </li>
    </ul>

    <address class="address">
      k7advisory<br>
      1420 Harbor View Road<br>
      Juneau, Alaska 99801
    </address>
  </section>

  <section class="card card--back" aria-label="Card back">
    <div class="brand-name">k7advisory</div>
    <div class="web-band">www.k7advisory.com</div>
  </section>
</main>
</body>
</html>
```